Residential Remodeling Contractor needs updated business card

I need a new design for my business card.
Name of the company is Ridgefell Construction. I need a card that commands presence, strength, integrity. I have been in business for 28 years. I am a Residential Remodeling Contractor that covers all aspects of a residential remodel and build.

```html
<!DOCTYPE html>
<html lang="en">
<head>
<meta charset="utf-8">
<title>Ridgefell Construction – Business Card</title>
<link href="https://fonts.googleapis.com/css2?family=Montserrat:wght@400;500;700&display=swap" rel="stylesheet">
<style>
  :root {
    --navy: #213f80;
    --navy-deep: #1c3672;
    --ink: #111111;
    --paper: #ffffff;
    --stage: #e6e7ea;
  }
  * { box-sizing: border-box; margin: 0; padding: 0; }
  html, body { width: 1200px; height: 900px; overflow: hidden; }
  body {
    background: var(--stage);
    font-family: "Montserrat", Arial, sans-serif;
    position: relative;
  }
  .card {
    position: absolute;
    left: 280px;
    width: 640px;
    height: 366px;
    overflow: hidden;
    box-shadow: 0 6px 18px rgba(0,0,0,0.18);
  }
  .card-back { top: 50px; background: var(--navy); }
  .card-front { top: 470px; background: var(--paper); }

  .back-brand {
    position: absolute; inset: 0;
    display: flex; align-items: center; justify-content: center; gap: 14px;
  }
  .back-brand .brand-mark { width: 22px; height: 22px; background: var(--navy-deep); filter: brightness(0.7); }
  .back-brand .brand-name {
    font-weight: 700; font-size: 30px; letter-spacing: 1px;
    color: #3557a8; text-transform: uppercase; line-height: 1.15;
  }

  .front-brand {
    position: absolute; left: 40px; top: 96px; width: 300px;
    display: flex; align-items: center; gap: 12px;
  }
  .front-brand .brand-mark { width: 20px; height: 20px; background: var(--navy); flex: none; }
  .front-brand .brand-name {
    font-weight: 700; font-size: 25px; color: var(--navy);
    text-transform: uppercase; line-height: 1.2; letter-spacing: 0.5px;
  }
  .divider {
    position: absolute; left: 358px; top: 80px; width: 1.5px; height: 118px;
    background: var(--navy);
  }
  .contact { position: absolute; left: 380px; top: 78px; color: var(--ink); }
  .contact .person-name {
    font-weight: 700; font-size: 21px; color: var(--navy); letter-spacing: 1.5px;
  }
  .contact .person-role { font-size: 12px; margin-top: 1px; margin-bottom: 12px; }
  .contact .address { font-size: 12px; line-height: 1.3; margin-bottom: 10px; }
  .contact .line { display: flex; align-items: center; gap: 6px; font-size: 12.5px; line-height: 1.45; }
  .contact .line svg { width: 11px; height: 11px; flex: none; }
  .contact .web-domain { color: var(--navy); }

  .wave { position: absolute; left: 0; bottom: 0; width: 640px; height: 150px; }
  .tagline {
    position: absolute; right: 54px; bottom: 22px;
    color: var(--paper); font-size: 12px; letter-spacing: 0.6px;
  }
</style>
</head>
<body>
  <section class="card card-back" aria-label="Card back">
    <div class="back-brand">
      <span class="brand-mark"></span>
      <span class="brand-name">Ridgefell<br>Construction</span>
    </div>
  </section>

  <section class="card card-front" aria-label="Card front">
    <div class="front-brand">
      <span class="brand-mark"></span>
      <span class="brand-name">Ridgefell<br>Construction</span>
    </div>
    <div class="divider"></div>
    <div class="contact">
      <div class="person-name">MARCUS DELANE</div>
      <div class="person-role">Director</div>
      <div class="address">482 Harlow Street Dunmore,<br>GA 30614</div>
      <div class="line">
        <svg viewBox="0 0 12 12"><path d="M3 1l2 2.5-1.2 1.2a6 6 0 0 0 3.5 3.5L8.5 7 11 9l-1.3 1.8C6 11 1 6 1.2 2.3z" fill="var(--navy)"/></svg>
        <span>(706) 555-0148</span>
      </div>
      <div class="line">
        <svg viewBox="0 0 12 12"><rect x="0.8" y="2.2" width="10.4" height="7.6" fill="none" stroke="var(--navy)" stroke-width="1.1"/><path d="M1 2.6l5 4 5-4" fill="none" stroke="var(--navy)" stroke-width="1.1"/></svg>
        <span>info@ridgefellbuild.com</span>
      </div>
      <div class="line">
        <svg viewBox="0 0 12 12"><circle cx="6" cy="6" r="5" fill="none" stroke="var(--navy)" stroke-width="1.1"/><ellipse cx="6" cy="6" rx="2.2" ry="5" fill="none" stroke="var(--navy)" stroke-width="1"/><path d="M1 6h10M2 3.5h8M2 8.5h8" stroke="var(--navy)" stroke-width="0.9"/></svg>
        <span>www.<span class="web-domain">ridgefellbuild</span>.com</span>
      </div>
    </div>
    <svg class="wave" viewBox="0 0 640 150" preserveAspectRatio="none" aria-hidden="true">
      <path d="M0 45 C150 85 380 50 640 125 L640 150 L0 150 Z" fill="var(--navy)"/>
      <path d="M10 50 C170 78 400 55 610 115" fill="none" stroke="var(--ink)" stroke-width="3"/>
    </svg>
    <div class="tagline">I have been in business for 28 years</div>
  </section>
</body>
</html>
```